Law firm business card

Information:

Me Mireille Dufontaine

website: dufontaine-legal.ca
email: mireille@dufontaine-legal.ca
Phone: 514 382-5167
Fax: 514 382-5169

Address:
Dufontaine and associates
2719 Belcourtier
Montreal, QC
H2K 3M9

Areas of Expertise:
Franchise Agreements, Financing, Acquisition, Real Estate Development, Commercial Agreements and Corporate Law

Target Market(s)

executives, companie managers

Industry/Entity Type

Business

Colors
f78f20
000000

Requirements
Must have
• Must use the logo, the logo is available here:

https://www.filecrate-example.com/sh/qyt3kwud82mfa0x/BBQTn7Lhvpe_kRTXwJM_GhcYb

```html
<!DOCTYPE html>
<html lang="en">
<head>
<meta charset="utf-8">
<title>Dufontaine and associates – Business Card</title>
<link rel="stylesheet" href="https://fonts.googleapis.com/css2?family=Montserrat:wght@600&family=Open+Sans:wght@400&display=swap">
<style>
  :root {
    --orange: #f78f20;
    --ink: #000000;
    --text-grey: #4a4a4a;
    --band-grey: #6e6e6e;
    --bar-grey: #c8c8c8;
    --mark-grey: #d9d9d9;
    --card: #ffffff;
    --backdrop: #e4e6e8;
  }
  * { box-sizing: border-box; margin: 0; padding: 0; }
  html, body { width: 1200px; height: 843px; overflow: hidden; }
  body {
    background: var(--backdrop);
    display: flex;
    flex-direction: column;
    align-items: center;
    justify-content: center;
    gap: 50px;
  }
  .card {
    position: relative;
    width: 600px;
    height: 343px;
    background: var(--card);
    box-shadow: 0 6px 18px rgba(0,0,0,.18);
    overflow: hidden;
  }
  .card-art { position: absolute; inset: 0; }

  /* brand lockup: name in the card's text face, one colour, one weight */
  .brand { position: absolute; display: flex; align-items: center; gap: 14px; }
  .brand-mark {
    width: 44px; height: 44px; flex: none;
    background: var(--mark-grey);
  }
  .brand-name {
    font-family: "Montserrat", sans-serif; font-weight: 600;
    color: var(--text-grey); font-size: 22px;
    line-height: 1.2; letter-spacing: .04em;
  }
  .brand-name span { display: block; }

  .card-back .brand { left: 50%; top: 50%; transform: translate(-50%, -50%); }
  .card-back .brand-mark { width: 56px; height: 56px; }
  .card-back .brand-name { font-size: 28px; }

  .card-front .brand { left: 34px; top: 122px; flex-direction: column; align-items: flex-start; gap: 10px; }

  /* person */
  .person { position: absolute; right: 34px; top: 76px; text-align: right; }
  .person-name {
    font-family: "Montserrat", sans-serif; font-weight: 600;
    font-size: 25px; letter-spacing: .06em; color: var(--text-grey);
  }
  .person-title {
    font-family: "Montserrat", sans-serif; font-weight: 600;
    font-size: 13px; letter-spacing: .08em; color: var(--ink);
    margin-top: 2px;
  }

  /* contact rows */
  .contacts { position: absolute; left: 318px; top: 150px; list-style: none; }
  .contact { display: flex; align-items: center; margin-bottom: 8px; }
  .contact-icon {
    width: 20px; height: 20px; border-radius: 50%;
    border: 1.5px solid var(--text-grey); flex: none;
    display: flex; align-items: center; justify-content: center;
    position: relative; z-index: 1; background: var(--card);
  }
  .contact-icon svg { width: 11px; height: 11px; }
  .contact-text {
    background: var(--bar-grey);
    border-radius: 0 9px 9px 0;
    margin-left: -4px;
    padding: 3px 12px;
    width: 230px;
    font-family: "Open Sans", sans-serif; font-size: 11px;
    color: var(--text-grey); line-height: 1.35;
  }
</style>
</head>
<body>

  <section class="card card-back" aria-label="Business card, back">
    <div class="brand">
      <span class="brand-mark"></span>
      <span class="brand-name"><span>Dufontaine</span><span>&amp; Associates</span></span>
    </div>
  </section>

  <section class="card card-front" aria-label="Business card, front">
    <svg class="card-art" viewBox="0 0 600 343" aria-hidden="true">
      <polygon points="0,0 270,0 254,16 0,16" fill="var(--band-grey)"/>
      <polygon points="282,0 288,0 272,16 266,16" fill="var(--band-grey)"/>
      <polygon points="294,0 300,0 284,16 278,16" fill="var(--band-grey)"/>
      <rect x="0" y="337" width="600" height="6" fill="var(--band-grey)"/>
      <polygon points="300,343 316,325 600,325 600,343" fill="var(--orange)"/>
      <polygon points="284,343 300,325 306,325 290,343" fill="var(--orange)"/>
      <polygon points="272,343 288,325 294,325 278,343" fill="var(--orange)"/>
    </svg>

    <div class="brand">
      <span class="brand-mark"></span>
      <span class="brand-name"><span>Dufontaine</span><span>&amp; Associates</span></span>
    </div>

    <div class="person">
      <h1 class="person-name">MIREILLE DUFONTAINE</h1>
      <p class="person-title">GENERAL MANAGER</p>
    </div>

    <ul class="contacts">
      <li class="contact">
        <span class="contact-icon"><svg viewBox="0 0 12 12"><path d="M3 1l2 2.5-1 1.2a6 6 0 0 0 3.3 3.3l1.2-1L11 9l-1 2C5 11 1 7 1 2z" fill="var(--text-grey)"/></svg></span>
        <span class="contact-text">514 382-5167</span>
      </li>
      <li class="contact">
        <span class="contact-icon"><svg viewBox="0 0 12 12"><rect x="2" y="4" width="8" height="6" rx="1" fill="none" stroke="var(--text-grey)" stroke-width="1.3"/><rect x="3.5" y="1.5" width="5" height="3" fill="none" stroke="var(--text-grey)" stroke-width="1.1"/></svg></span>
        <span class="contact-text">514 382-5169</span>
      </li>
      <li class="contact">
        <span class="contact-icon"><svg viewBox="0 0 12 12"><rect x="1" y="2.5" width="10" height="7" rx="1" fill="none" stroke="var(--text-grey)" stroke-width="1.3"/><path d="M1.5 3l4.5 3.5L10.5 3" fill="none" stroke="var(--text-grey)" stroke-width="1.2"/></svg></span>
        <span class="contact-text">mireille@dufontaine-legal.ca</span>
      </li>
      <li class="contact">
        <span class="contact-icon"><svg viewBox="0 0 12 12"><circle cx="6" cy="6" r="4.8" fill="none" stroke="var(--text-grey)" stroke-width="1.2"/><path d="M1.2 6h9.6M6 1.2c-2.5 3-2.5 6.6 0 9.6M6 1.2c2.5 3 2.5 6.6 0 9.6" fill="none" stroke="var(--text-grey)" stroke-width=".9"/></svg></span>
        <span class="contact-text">dufontaine-legal.ca</span>
      </li>
      <li class="contact">
        <span class="contact-icon"><svg viewBox="0 0 12 12"><path d="M6 11s-3.8-4-3.8-6.5a3.8 3.8 0 0 1 7.6 0C9.8 7 6 11 6 11z" fill="var(--text-grey)"/><circle cx="6" cy="4.6" r="1.3" fill="var(--card)"/></svg></span>
        <span class="contact-text">2719 Belcourtier, Montreal, QC<br>H2K 3M9</span>
      </li>
    </ul>
  </section>

</body>
</html>
```